Website for new crypto research organization

See brief (attached). This is a pretty basic website with only a handful of pages + ability to collect email addresses.

```html
<!DOCTYPE html>
<html lang="en">
<head>
<meta charset="utf-8">
<title>Tealstone Digital</title>
<link href="https://fonts.googleapis.com/css2?family=IBM+Plex+Sans:wght@400;500;600&family=Montserrat:wght@500;600;700&display=swap" rel="stylesheet">
<style>
:root{
  --teal:#1b998b;
  --teal-light:#7fd3c8;
  --blue:#2594c9;
  --footer:#2aa0d8;
  --ink:#222;
  --body:#3a3a3a;
  --gray:#f4f4f4;
  --white:#fff;
}
*{margin:0;padding:0;box-sizing:border-box}
html,body{width:1200px;height:2848px;overflow:hidden}
body{position:relative;background:var(--white);font-family:"IBM Plex Sans",sans-serif;color:var(--body)}
.abs{position:absolute}
.brand{font-family:"Montserrat",sans-serif;font-weight:600;color:var(--teal);font-size:16px;display:flex;align-items:center;gap:8px}
.brand .mark{width:14px;height:14px;background:var(--teal)}
.site-header{left:0;top:0;width:1200px;height:84px;background:var(--white)}
.site-header .brand{left:112px;top:30px}
.main-nav{right:113px;top:34px;display:flex;gap:29px;font-size:15px;color:#333}
.main-nav .active{border-bottom:2px solid var(--teal);padding-bottom:5px}
.hero{left:0;top:84px;width:1200px;height:620px;background:linear-gradient(115deg,#2a7fc6 0%,#3db7d8 25%,#e0532c 45%,#8a4fbf 65%,#8fd43a 85%,#7b5ac9 100%)}
.hero-title{left:110px;top:258px;font-family:"Montserrat",sans-serif;font-weight:700;color:var(--white);font-size:48px;line-height:1}
.hero-sub{left:112px;top:318px;font-family:"Montserrat",sans-serif;font-weight:700;color:var(--white);font-size:32px;letter-spacing:22px}
.hero-tag{left:110px;top:372px;color:var(--white);font-size:20px;font-weight:500}
.btn-start{left:110px;top:418px;width:185px;height:48px;background:var(--white);color:#111;font-weight:600;font-size:15px;display:flex;align-items:center;justify-content:center}
.slider-dots{left:1139px;top:344px;display:flex;flex-direction:column;gap:11px}
.slider-dots span{width:8px;height:8px;border-radius:50%;background:var(--white)}
.hero-wave{left:0;top:600px}
.about{left:0;top:700px;width:1200px;height:284px;background:var(--gray);text-align:center}
.section-title{font-family:"Montserrat",sans-serif;font-weight:600;font-size:28px}
.about .section-title{margin-top:68px;color:var(--ink)}
.about p{width:820px;margin:18px auto 0;font-size:15px;line-height:26px}
.link-more{display:inline-flex;align-items:center;gap:8px;font-weight:500;font-size:15px;color:var(--teal)}
.about .link-more{margin-top:20px}
.copy{font-size:15px;line-height:24px;width:420px}
.teal-frame{background:var(--teal)}
.photo{}
.process-title{left:110px;top:1108px;color:var(--teal);font-size:31px}
.process-text{left:110px;top:1160px}
.process-more{left:110px;top:1325px}
.research{left:0;top:1476px;width:1200px;height:464px;background:var(--gray)}
.research .section-title{position:absolute;top:42px;width:100%;text-align:center;color:var(--teal);font-size:30px}
.research-grid{position:absolute;left:0;top:92px;width:1200px;height:306px;border-top:1px solid var(--teal);border-bottom:1px solid var(--teal)}
.research-grid .divider{position:absolute;top:0;width:1px;height:100%;background:var(--teal)}
.card{position:absolute;top:0}
.card .date{margin-top:26px;font-size:17px;color:#222}
.tags{margin-top:22px;display:flex;flex-wrap:wrap;width:310px;gap:14px 6px}
.tag{width:94px;height:30px;background:var(--teal);color:var(--white);font-size:15px;font-weight:500;display:flex;align-items:center;justify-content:center}
.tag.alt{background:var(--blue)}
.card h3{margin-top:20px;font-family:"Montserrat",sans-serif;font-weight:500;font-size:20px;line-height:29px;color:#222}
.card .link-more{margin-top:16px;color:#222}
.careers-title{left:643px;top:2062px;color:var(--teal);font-size:33px}
.careers-text{left:646px;top:2122px;width:420px}
.careers-more{left:646px;top:2274px}
.footer{left:0;top:2400px;width:1200px;height:448px}
.footer .brand{position:absolute;left:530px;top:150px;width:140px;height:66px;border:2px solid var(--white);color:var(--white);justify-content:center;font-size:17px}
.follow{position:absolute;top:233px;left:0;width:1200px;display:flex;justify-content:center;align-items:center;gap:10px;color:var(--white);font-size:17px;font-weight:500}
.follow .sq{width:18px;height:18px;background:var(--white);border-radius:3px}
.follow .sq:first-of-type{margin-left:12px}
.foot-nav{position:absolute;top:274px;left:0;width:1200px;display:flex;justify-content:center;gap:29px;color:var(--white);font-size:15px}
.subscribe{position:absolute;left:349px;top:306px;width:502px;height:42px;background:var(--white);border-radius:21px}
.subscribe span{position:absolute;left:31px;top:11px;color:#aaa;font-size:14px}
.subscribe b{position:absolute;right:0;top:0;width:188px;height:42px;border-radius:21px;background:var(--teal);color:var(--white);font-size:15px;font-weight:600;display:flex;align-items:center;justify-content:center;border:2px solid var(--white)}
.foot-rule{position:absolute;left:111px;top:378px;width:978px;height:1px;background:rgba(255,255,255,.8)}
.copyright{position:absolute;top:401px;width:1200px;text-align:center;color:var(--white);font-size:15px}
</style>
</head>
<body>
<header class="site-header abs">
  <div class="brand abs"><span class="mark"></span>Tealstone Digital</div>
  <nav class="main-nav abs"><span class="active">Home</span><span>About</span><span>Research</span><span>News</span><span>Careers</span><span>Contact</span></nav>
</header>

<section class="hero abs" role="img" aria-label="Colourful graffiti wall with swirling blue, green, red and purple shapes"></section>
<div class="hero-title abs">TEALSTONE</div>
<div class="hero-sub abs">DIGITAL</div>
<div class="hero-tag abs">Neque Porro Quisquam Est, Qui</div>
<div class="btn-start abs">GET STARTED</div>
<div class="slider-dots abs"><span></span><span></span><span></span></div>
<svg class="hero-wave abs" width="1200" height="110" viewBox="0 600 1200 110">
  <path d="M0 680 C40 640 90 620 150 632 C260 650 360 700 480 694 C600 688 680 648 790 652 C900 656 960 700 1060 694 C1130 690 1170 660 1200 625 L1200 710 L0 710 Z" fill="var(--gray)"/>
  <path d="M0 680 C40 640 90 620 150 632 C260 650 360 700 480 694 C600 688 680 648 790 652 C900 656 960 700 1060 694 C1130 690 1170 660 1200 625" fill="none" stroke="var(--teal)" stroke-width="5"/>
</svg>

<section class="about abs">
  <h2 class="section-title">ABOUT US</h2>
  <p>But I Must Explain To You How All This Mistaken Idea Of Denouncing Pleasure And Praising Pain Was Born And I Will Give You A Complete Account Of The System, And Expound The Actual Teachings Of The Great Explorer Truth, The Master-builder Of Human Happiness. No One Rejects, Dislikes, Or Avoids Pleasure</p>
  <div class="link-more">MEET THE TEAM <svg width="22" height="10"><path d="M0 5H20M15 1L20 5L15 9" stroke="var(--teal)" fill="none" stroke-width="1.6"/></svg></div>
</section>

<h2 class="section-title process-title abs">OUR RESEARCH PROCESS</h2>
<p class="copy process-text abs">But I Must Explain To You How All This Mistaken Idea Of Denouncing Pleasure And Praising Pain Was Born And I Will Give You A Complete Account Of The System, And Expound The Actual Teachings Of The Great Explorer Of The Truth, The Master-builder Of Human Happiness. No One Rejects, Dislikes, Or Avoids Pleasure Itself, Because It Is Pleasure,</p>
<div class="link-more process-more abs">READ MORE <svg width="22" height="10"><path d="M0 5H20M15 1L20 5L15 9" stroke="var(--teal)" fill="none" stroke-width="1.6"/></svg></div>
<div class="teal-frame abs" style="left:607px;top:1074px;width:467px;height:294px"></div>
<div class="photo abs" style="left:619px;top:1086px;width:467px;height:295px;background:radial-gradient(circle at 35% 50%,#e8c26a 0,#a57a35 14%,#1b3f8a 32%,#0d1f4f 70%,#08163a 100%)" role="img" aria-label="Golden digital coin glowing on a dark blue technology background"></div>

<section class="research abs">
  <h2 class="section-title">RESEARCH</h2>
  <div class="research-grid">
    <div class="divider" style="left:425px"></div>
    <div class="divider" style="left:770px"></div>
    <div class="card" style="left:110px">
      <div class="date">28.1.2022</div>
      <div class="tags"><span class="tag">Pleasure</span><span class="tag alt">Except</span><span class="tag">Great</span><span class="tag">Pursues</span><span class="tag alt">Human</span></div>
      <h3>Beacon Network<br>valuations : Resultant</h3>
      <div class="link-more">READ MORE <svg width="22" height="10"><path d="M0 5H20M15 1L20 5L15 9" stroke="var(--teal)" fill="none" stroke-width="1.6"/></svg></div>
    </div>
    <div class="card" style="left:449px">
      <div class="date">10.1.2022</div>
      <div class="tags"><span class="tag">Pleasure</span><span class="tag alt">Except</span><span class="tag">Great</span><span class="tag">Pursues</span><span class="tag alt">Human</span></div>
      <h3>Satchel Network<br>investment thesis</h3>
      <div class="link-more">READ MORE <svg width="22" height="10"><path d="M0 5H20M15 1L20 5L15 9" stroke="var(--teal)" fill="none" stroke-width="1.6"/></svg></div>
    </div>
    <div class="card" style="left:786px">
      <div class="date">15.1.2022</div>
      <div class="tags"><span class="tag">Pleasure</span><span class="tag alt">Except</span><span class="tag">Great</span><span class="tag">Pursues</span><span class="tag alt">Human</span></div>
      <h3>The Regulatory State<br>22 Resultant for 2022</h3>
      <div class="link-more">READ MORE <svg width="22" height="10"><path d="M0 5H20M15 1L20 5L15 9" stroke="var(--teal)" fill="none" stroke-width="1.6"/></svg></div>
    </div>
  </div>
</section>

<div class="teal-frame abs" style="left:111px;top:2025px;width:467px;height:293px"></div>
<div class="photo abs" style="left:122px;top:2037px;width:467px;height:296px;background:linear-gradient(120deg,#2a3d63 0%,#4a6794 35%,#c9a488 55%,#3b5a8c 75%,#dfe6ee 100%)" role="img" aria-label="Hands holding a glowing financial candlestick chart"></div>
<h2 class="section-title careers-title abs">CAREERS</h2>
<p class="copy careers-text abs">But I Must Explain To You How All This Mistaken Idea Of Denouncing Pleasure And Praising Pain Was Born And I Will Give You A Complete Account Of The System, And Expound The Actual Teachings Of The Great Explorer Of The Truth, The Master-builder Of Human Happiness. No One Rejects, Dislikes, Or Avoids Pleasure Itself, Because It Is Pleasure,</p>
<div class="link-more careers-more abs">READ MORE <svg width="22" height="10"><path d="M0 5H20M15 1L20 5L15 9" stroke="var(--teal)" fill="none" stroke-width="1.6"/></svg></div>

<footer class="footer abs">
  <svg class="abs" style="left:0;top:0" width="1200" height="448" viewBox="0 2400 1200 448">
    <path d="M0 2497 C60 2460 130 2425 220 2431 C320 2438 380 2490 480 2486 C580 2482 640 2430 760 2440 C860 2448 930 2500 1040 2496 C1110 2494 1170 2460 1200 2420 L1200 2848 L0 2848 Z" fill="var(--footer)"/>
    <path d="M0 2497 C60 2460 130 2425 220 2431 C320 2438 380 2490 480 2486 C580 2482 640 2430 760 2440 C860 2448 930 2500 1040 2496 C1110 2494 1170 2460 1200 2420" fill="none" stroke="var(--teal-light)" stroke-width="8"/>
  </svg>
  <div class="brand">Tealstone Digital</div>
  <div class="follow">FOLLOW UP <span class="sq"></span><span class="sq"></span></div>
  <nav class="foot-nav"><span>Home</span><span>About</span><span>Research</span><span>News</span><span>Careers</span><span>Contact</span></nav>
  <div class="subscribe"><span>Type your Email</span><b>RESEARCH REPORT</b></div>
  <div class="foot-rule"></div>
  <div class="copyright">CopyRights @2022 Tealstone digital.All rights Reserved.</div>
</footer>
</body>
</html>
```